Dental Practice Website design

Design a new website for Brambleford Dental Practice.
Design should be warm, neutral in colour, with some small amount of bright colour if needed but kept to a minimum. Website should look professional, high end. Home page should be easy to navigate and simple for patients to be able to book online.
Logo in files along with some examples of websites that we like. Please ask if any further info needed.
Menu should have:
About
New Patients
Treatments
Fees
Contact Us

Industry/Entity Type

Dentistry

Number of Pages Required

4 page

Font styles to use
Sans Serif

Colors

Designer to choose colors to be used in the design.

Requirements
Must have
• Ravelle ratings badge, book online button,
Nice to have
• neutral, relaxing colours
Should not have
• harsh, bright colours!

```html
<!DOCTYPE html>
<html lang="en">
<head>
<meta charset="utf-8">
<title>Brambleford Dental Practice</title>
<link href="https://fonts.googleapis.com/css2?family=Oswald:wght@300;400;500&family=Poppins:wght@400;500;600&family=Roboto:wght@300;400;500;700&display=swap" rel="stylesheet">
<style>
:root{
  --ink:#17272b;
  --sky:#cfe8fb;
  --blue:#6aa8e8;
  --blue-soft:#8ec0f0;
  --taupe:#8c7b68;
  --taupe-light:#a49480;
  --cream:#fbf5ec;
  --sand:#f3ece1;
  --gold:#dcb43f;
  --text:#2b2b2b;
  --muted:#555;
  --white:#fff;
}
*{box-sizing:border-box;margin:0;padding:0}
html,body{width:1200px;height:5047px;overflow:hidden}
body{font-family:"Roboto",sans-serif;color:var(--text);background:var(--white)}
section,header,footer{position:relative;width:1200px;overflow:hidden}
.abs{position:absolute}
.photo{position:absolute}
.btn{position:absolute;display:flex;align-items:center;justify-content:center;border-radius:30px;font-family:"Roboto",sans-serif;font-weight:500;font-size:13px;text-transform:uppercase}

/* header */
.site-header{height:143px;background:var(--ink);color:var(--white)}
.brand{left:55px;top:14px;width:180px;font-family:"Roboto",sans-serif;font-weight:300;color:#cfd6d8}
.brand .mark{width:170px;height:56px;border:1.5px solid #cfd6d8;margin-bottom:4px}
.brand .name{font-size:20px;letter-spacing:1px;line-height:1.05;text-transform:uppercase}
.call{left:770px;top:40px;font-size:13px;letter-spacing:.5px}
.appt{left:962px;top:27px;width:186px;height:42px;background:var(--sand);color:var(--ink);font-size:12px}
.nav{right:52px;top:92px;display:flex;gap:19px;font-size:13px;text-transform:uppercase}

/* hero */
.hero{height:684px;background:var(--sky)}
.hero .photo{left:0;top:0;width:690px;height:684px;background:linear-gradient(120deg,#a9c9df,#d9bfa5 55%,#6f8fb4)}
.hero h1{left:717px;top:132px;width:470px;font-family:"Poppins",sans-serif;font-weight:600;font-size:39px;line-height:1.15;color:var(--ink)}
.hero .lead{left:719px;top:238px;width:430px;font-size:14px;line-height:1.65;color:#333}
.hero .rule{left:719px;top:307px;width:428px;height:1px;background:#9fb8c9}
.stats{left:723px;top:328px;display:flex;gap:0}
.stat{width:172px}
.stat b{display:block;font-family:"Poppins",sans-serif;font-weight:500;font-size:38px;color:var(--ink);line-height:1.1}
.stat span{font-size:12px;color:#333}
.hero .rule2{left:719px;top:412px}
.book-online{left:726px;top:452px;width:156px;height:50px;background:var(--blue);color:var(--ink)}
.enquire{left:893px;top:452px;width:158px;height:50px;background:var(--ink);color:var(--blue-soft)}

/* welcome */
.welcome{height:743px}
.welcome .kicker{left:55px;top:76px;font-family:"Oswald",sans-serif;font-size:24px;color:var(--blue);text-transform:uppercase}
.welcome h2{left:55px;top:104px;font-family:"Oswald",sans-serif;font-weight:400;font-size:40px;color:var(--ink);text-transform:uppercase}
.welcome .copy{left:55px;top:174px;width:388px;font-size:11.5px;line-height:1.55;text-align:justify;color:#333}
.welcome .copy p{margin-bottom:13px}
.welcome .dark-btn{left:55px;top:541px;width:182px;height:50px;background:var(--ink);color:var(--white)}
.welcome .photo-main{left:612px;top:66px;width:536px;height:608px;background:linear-gradient(160deg,#e9e4df,#c9b5a3 50%,#a9cbe6)}
.welcome .photo-tilt{left:474px;top:300px;width:270px;height:310px;transform:rotate(-8deg);background:linear-gradient(150deg,#d8c8b0,#e3c24f 60%,#7b8c9a);border:6px solid var(--white)}

/* services */
.services{height:250px;height:520px}
.card{position:absolute;top:30px;width:356px;height:440px;text-align:center;color:var(--white)}
.card .icon{width:114px;height:114px;border-radius:50%;background:#f4ece1;margin:48px auto 0;display:flex;align-items:center;justify-content:center}
.card h3{font-family:"Roboto",sans-serif;font-weight:400;font-size:19px;margin-top:20px}
.card p{width:280px;margin:22px auto 0;font-size:11px;line-height:1.8;opacity:.95}
.card .more{position:relative;display:inline-flex;margin-top:26px;width:150px;height:44px;border-radius:24px;background:#eee3d6;color:#7a6a58;align-items:center;justify-content:center;font-size:11.5px;text-transform:uppercase}
.card.taupe{background:var(--taupe-light)}
.card.blue{background:var(--blue)}
.card.blue .icon{background:#e9f3fd}
.card.blue .more{background:#e9f3fd;color:var(--blue)}
.card.dark{background:var(--taupe)}

/* join */
.join{height:564px;background:linear-gradient(90deg,#e8e1da,#f3efe9 55%,#f7f4ef)}
.join .photo{left:0;top:0;width:610px;height:564px;background:linear-gradient(120deg,#3b2a22,#b58a6a 45%,#d9d2c7)}
.join h2{left:600px;top:88px;width:560px;text-align:center;font-family:"Oswald",sans-serif;font-weight:400;font-size:38px;color:var(--ink);text-transform:uppercase}
.join .copy{left:616px;top:150px;width:534px;text-align:center;font-size:12.5px;line-height:1.65;color:#333}
.join .copy p{margin-bottom:15px}
.join .outline{left:818px;top:420px;width:148px;height:46px;border:1.5px solid var(--ink);color:var(--ink)}

/* team */
.team{height:752px}
.team h2{left:0;top:42px;width:1200px;text-align:center;font-family:"Oswald",sans-serif;font-weight:400;font-size:40px;color:var(--ink);text-transform:uppercase}
.team .intro{left:100px;top:120px;width:1000px;text-align:center;font-size:11.5px;line-height:1.9;color:#333}
.member{position:absolute;top:243px;width:252px;height:442px;border:1px solid #e6e6e6;background:var(--white)}
.member .photo{left:0;top:0;width:250px;height:278px}
.member h4{position:absolute;left:12px;top:290px;font-size:13px;font-weight:500}
.member .role{position:absolute;left:12px;top:312px;font-size:10px;color:#666}
.member .bio{position:absolute;left:12px;top:334px;width:226px;font-size:9.5px;line-height:1.65;color:#444}
.member .social{position:absolute;left:12px;top:392px;display:flex;gap:14px}
.member .social i{width:22px;height:22px;border:1px solid #ccc;border-radius:50%}

/* reviews */
.reviews{height:608px;background:var(--cream)}
.reviews .photo{left:612px;top:0;width:588px;height:608px;background:linear-gradient(150deg,#ebe3dc,#d9b991 50%,#f1ece6)}
.reviews .kicker{left:0;top:120px;width:612px;text-align:center;font-family:"Roboto",sans-serif;font-size:30px;letter-spacing:1px;color:var(--ink)}
.reviews h2{left:0;top:150px;width:652px;text-align:center;font-family:"Roboto",sans-serif;font-weight:700;font-size:64px;color:var(--ink)}
.reviews .copy{left:80px;top:240px;width:492px;text-align:center;font-size:13px;line-height:1.75;color:#333}
.stars{left:0;top:361px;width:652px;display:flex;justify-content:center;gap:6px}
.reviews .gold{left:214px;top:424px;width:224px;height:62px;background:var(--gold);color:var(--white);border-radius:32px;font-size:14px}

/* contact */
.contact{height:648px}
.contact .photo{left:0;top:0;width:612px;height:648px;background:linear-gradient(140deg,#6b5a4f,#e2925a 50%,#e8d9c8)}
.contact h2{left:678px;top:72px;font-family:"Roboto",sans-serif;font-weight:700;font-size:37px;color:var(--ink)}
.field{position:absolute;left:681px;width:467px;height:54px;border:1px solid #cfcfcf;font-size:11px;color:#888;padding:17px 22px}
.field.msg{height:98px}
.submit{position:absolute;left:683px;top:534px;width:465px;height:62px;background:var(--taupe);color:var(--white);display:flex;align-items:center;justify-content:center;font-weight:700;font-size:22px;text-transform:uppercase}

/* footer */
.site-footer{height:310px;background:var(--ink);color:var(--white)}
.foot-brand{left:58px;top:66px;color:#cfd6d8;font-weight:300}
.foot-brand .mark{width:246px;height:80px;border:1.5px solid #cfd6d8;margin-bottom:6px}
.foot-brand .name{font-size:28px;line-height:1.05;letter-spacing:1px;text-transform:uppercase}
.foot h5{font-size:16px;font-weight:500;text-transform:uppercase}
.links{left:495px;top:70px}
.links ul{list-style:none;display:grid;grid-template-columns:154px 150px;row-gap:16px;margin-top:24px;font-size:11px}
.links li::before{content:"\203A  ";}
.news{left:882px;top:70px;width:266px}
.news p{font-size:11px;line-height:1.6;margin-top:18px}
.news .email{width:266px;height:40px;background:#eef6fd;margin-top:16px;color:#9bb;font-size:10px;padding:13px 16px}
.news .sub{width:266px;height:42px;background:var(--blue);margin-top:8px;display:flex;align-items:center;justify-content:center;font-weight:700;font-size:14px;text-transform:uppercase}
.bottom-bar{height:80px;background:var(--blue);color:var(--white)}
.bottom-bar .copy{left:55px;top:32px;font-size:11px}
.bottom-bar .social{right:52px;top:25px;display:flex;gap:9px}
.bottom-bar .social i{width:28px;height:28px;border:1.5px solid var(--white);border-radius:50%}
</style>
</head>
<body>

<header class="site-header">
  <div class="abs brand"><div class="mark"></div><div class="name">Brambleford<br>Dental Practice</div></div>
  <div class="abs call">CALL TODAY 263 555 0142</div>
  <div class="btn appt">Book an appointment</div>
  <nav class="abs nav"><span>Home</span><span>About</span><span>New Patients</span><span>Treatments</span><span>Fees</span><span>Contact Us</span></nav>
</header>

<section class="hero">
  <div class="photo" role="img" aria-label="Smiling couple embracing, wearing denim shirts"></div>
  <h1 class="abs">Cosmetic and Beauty Dentistry Trend Today</h1>
  <p class="abs lead">Experience top-quality dental care focused on your smile's health and beauty. Trust us to create a brighter, healthier tomorrow.</p>
  <div class="abs rule"></div>
  <div class="abs stats">
    <div class="stat"><b>24X7</b><span>Emergency Service</span></div>
    <div class="stat"><b>25k</b><span>Recover Patient</span></div>
    <div class="stat"><b>15+</b><span>Market Experience</span></div>
  </div>
  <div class="abs rule rule2"></div>
  <div class="btn book-online">Book Online</div>
  <div class="btn enquire">Enquire Now</div>
</section>

<section class="welcome">
  <div class="abs kicker">Welcome to</div>
  <h2 class="abs">Brambleford Dental Practice</h2>
  <div class="abs copy">
    <p>Welcome to our friendly dental practice nestled in the heart of beautiful Ashcombe, UK. Our team of dedicated dentists, hygienists and support staff are here to provide you with exceptional dental care. With a wide array of services, including general and cosmetic dentistry, orthodontics and emergency care, we're confident that we can deliver the highest quality treatment to you and your loved ones.</p>
    <p>At our practice, we believe that a visit to the dentist should be a comfortable and positive experience. We strive to create a warm and welcoming atmosphere where our patients can feel at ease and confident in the care they receive. Our state-of-the-art facilities and equipment mean that you can trust us to deliver the latest techniques and treatments to ensure your oral health is at its best.</p>
    <p>We are passionate about improving dental health and helping you achieve your brightest smile and are honoured that you're considering us for your dental needs. Please don't hesitate to contact us if you have any questions or to schedule an appointment. We look forward to welcoming you to our practice.</p>
  </div>
  <div class="btn dark-btn">Book Online</div>
  <div class="photo photo-main" role="img" aria-label="Smiling woman in a blue top holding a dental model"></div>
  <div class="photo photo-tilt" role="img" aria-label="Happy senior couple smiling together"></div>
</section>

<section class="services">
  <div class="card taupe" style="left:55px">
    <div class="icon"><svg width="58" height="58" viewBox="0 0 58 58" fill="none" stroke="#a49480" stroke-width="2"><path d="M14 12c6-4 10 0 15 0s9-4 15 0c5 4 4 14 1 20-2 5-3 16-6 18-3 1-4-12-10-12s-7 13-10 12c-3-2-4-13-6-18-3-6-4-16 1-20z"/></svg></div>
    <h3>General Dentistry</h3>
    <p>Lorem Ipsum is simply dummy text of the printing when an unknown printer took a galley of type and scrambled it to make a type specimen book. It has survived not only recently with desktop publishing software like Quillset Layout including versions of Lorem Ipsum.</p>
    <div class="more">Read More</div>
  </div>
  <div class="card blue" style="left:425px">
    <div class="icon"><svg width="58" height="58" viewBox="0 0 58 58" fill="none" stroke="#6aa8e8" stroke-width="2"><circle cx="29" cy="22" r="12"/><path d="M10 52c2-10 10-15 19-15s17 5 19 15"/><path d="M38 30l8 8"/></svg></div>
    <h3>Cosmetic Dentistry</h3>
    <p>Lorem Ipsum is simply dummy text of the printing when an unknown printer took a galley of type and scrambled it to make a type specimen book. It has survived not only recently with desktop publishing software like Quillset Layout including versions of Lorem Ipsum.</p>
    <div class="more">Read More</div>
  </div>
  <div class="card dark" style="left:793px">
    <div class="icon"><svg width="58" height="58" viewBox="0 0 58 58" fill="none" stroke="#8c7b68" stroke-width="2"><path d="M14 12c6-4 10 0 15 0s9-4 15 0c5 4 4 14 1 20-2 5-3 16-6 18-3 1-4-12-10-12s-7 13-10 12c-3-2-4-13-6-18-3-6-4-16 1-20z"/><path d="M10 24h38"/><rect x="18" y="20" width="7" height="8"/><rect x="33" y="20" width="7" height="8"/></svg></div>
    <h3>Teeth Straightening</h3>
    <p>Lorem Ipsum is simply dummy text of the printing when an unknown printer took a galley of type and scrambled it to make a type specimen book. It has survived not only recently with desktop publishing software like Quillset Layout including versions of Lorem Ipsum.</p>
    <div class="more">Read More</div>
  </div>
</section>

<section class="join">
  <div class="photo" role="img" aria-label="Laughing couple hugging outdoors"></div>
  <h2 class="abs">Join Our Practice</h2>
  <div class="abs copy">
    <p>If you're looking for an exceptional dental practice, we're here to help! Our team is made up of highly skilled professionals who are dedicated to ensuring that all our patients receive top-notch care in a welcoming and comfortable environment.</p>
    <p>Whether you need a routine examination or a more specialised treatment, we have all the resources to provide you with the best dental care possible. Our practice is always up-to-date with the latest techniques and technologies to make sure that our patients receive the best possible results.</p>
    <p>We understand that dental care can be expensive which is why we offer affordable prices to ensure that everyone has access to quality care. If you'd like to learn more about our practice, please don't hesitate to contact us.</p>
  </div>
  <div class="btn outline">Join Now</div>
</section>

<section class="team">
  <h2 class="abs">Our Team</h2>
  <div class="abs intro">We are delighted to introduce you to our experienced and compassionate dental team. Our team comprises highly skilled dental professionals who are dedicated to providing you with high-quality dental services. Led by our experienced dentist, each member of our team brings their own unique set of skills and expertise.<br>From our friendly reception staff to our knowledgeable hygienists and assistants, our team is here to ensure that you receive personalised dental care that meets your unique needs and preferences. We take great pride in providing a safe, comfortable, and welcoming environment for our patients, and we look forward to serving you with the utmost care and attention.</div>
  <div class="member" style="left:56px"><div class="photo" role="img" aria-label="Portrait of a blonde team member in a cardigan" style="background:linear-gradient(160deg,#8a9b6e,#d8c3a8 55%,#9e8b7a)"></div><h4>Elena Marsh</h4><div class="role">Managing Director</div><div class="bio">Lorem Ipsum is simply dummy text printing and typesetting industry lorem Ipsum has been the industry's standard dummy text</div><div class="social"><i></i><i></i><i></i></div></div>
  <div class="member" style="left:337px"><div class="photo" role="img" aria-label="Portrait of a smiling man in a checked shirt" style="background:linear-gradient(160deg,#6d7378,#b79a84 50%,#5d7e86)"></div><h4>Oliver Grant</h4><div class="role">Software Engineer</div><div class="bio">Lorem Ipsum is simply dummy text printing and typesetting industry. Lorem Ipsum has been the industry's standard dummy text</div><div class="social"><i></i><i></i><i></i></div></div>
  <div class="member" style="left:616px"><div class="photo" role="img" aria-label="Portrait of a smiling woman with long wavy hair" style="background:linear-gradient(160deg,#cdbba8,#8f6a52 50%,#b9a08b)"></div><h4>Oliver Grant</h4><div class="role">Software Engineer</div><div class="bio">Lorem Ipsum is simply dummy textprinting and typesetting industry. Lorem Ipsum has been the industry's standard dummy text</div><div class="social"><i></i><i></i><i></i></div></div>
  <div class="member" style="left:896px"><div class="photo" role="img" aria-label="Portrait of a grey-haired man in a denim jacket" style="background:linear-gradient(160deg,#7d8f54,#c9a98c 50%,#3f5777)"></div><h4>Henry Vale</h4><div class="role">Software Engineer</div><div class="bio">Lorem Ipsum is simply dummy textprinting and typesetting industry. Lorem Ipsum has been the industry's standard dummy text</div><div class="social"><i></i><i></i><i></i></div></div>
</section>

<section class="reviews">
  <div class="abs kicker" style="width:652px">PATIENT</div>
  <h2 class="abs">REVIEWS</h2>
  <p class="abs copy">Lorem Ipsum is simply dummy text of the printing and typesetting industry. Lorem Ipsum has been the industry's standard dummy text ever since the 1500s, when an unknown printer took a galley of type and scrambled it to make a type specimen book. It has survived not only five centuries, but also the leap into electronic typesetting, remaining essentially unchanged.</p>
  <div class="abs stars">
    <svg width="140" height="24" viewBox="0 0 140 24" fill="#dcb43f"><g id="s"><path d="M12 1l3.2 7 7.6.8-5.7 5.1 1.6 7.5L12 17.6 5.3 21.4l1.6-7.5L1.2 8.8l7.6-.8z"/></g><use href="#s" x="28"/><use href="#s" x="56"/><use href="#s" x="84"/><use href="#s" x="112"/></svg>
  </div>
  <div class="btn gold">Read More Reviews</div>
  <div class="photo" role="img" aria-label="Smiling blonde woman with hand on cheek"></div>
</section>

<section class="contact">
  <div class="photo" role="img" aria-label="Laughing woman in an orange top holding a phone"></div>
  <h2 class="abs">GET IN TOUCH</h2>
  <div class="field" style="top:134px">Enter your name</div>
  <div class="field" style="top:204px">Enter your phone</div>
  <div class="field" style="top:274px">Enter your email</div>
  <div class="field" style="top:346px">Treatment Of Interest</div>
  <div class="field msg" style="top:418px">Enter your message</div>
  <div class="submit">Submit Now</div>
</section>

<footer class="site-footer foot">
  <div class="abs foot-brand"><div class="mark"></div><div class="name">Brambleford<br>Dental Practice</div></div>
  <div class="abs links"><h5>Quick Links</h5>
    <ul><li>Home</li><li>Fees</li><li>About Us</li><li>Contact Us</li><li>New Patients</li><li>Terms Of Services</li><li>Treatments</li><li>Privacy Policy</li></ul>
  </div>
  <div class="abs news"><h5>Newsletter</h5><p>Be Rewarded With Exclusive Member Offers, Including Discounts.</p><div class="email">Enter Your Email</div><div class="sub">Subscribe Now</div></div>
</footer>
<div class="bottom-bar" style="position:relative;width:1200px">
  <div class="abs copy">© 2025 bramblefordpractice.com. All Rights Reserved</div>
  <div class="abs social"><i></i><i></i><i></i></div>
</div>

</body>
</html>
```